Packaged Food Business Needs a Packaging Design

We need a package design to be used as a label/sticker on the lids of round and square transparent plastic containers and on the sides of resealable stand-up pouches. The brand name is 'Savorine' - please find attached logo together with pictures of the sample containers and pouch. We will use the packaging to market a wide variety of food categories from nuts, dried fruits, spices, cooking chocolates, baking ingredients, cereals, grains and pulses.

OVERALL FEEDBACK ON DESIGNS ALREADY RECEIVED:

- We have found so far that a lot of our mandatory requirements are not adhered to in designs that have been submitted so far. We would like to emphasise that the ingredient, weight and expiry text will be printed at the time of packing so it should not take prime space on the pack BUT at the same time some 'blank' space needs to flawlessly be incorporated into the overall design for this purpose
- We encourage you to glorify the brand logo in the pack, and absolutely refrain from duplicating the tagline
- Please note that ONE label design will be used to pack a wide variety of food ingredients and therefore please ensure that the choice of your design incorporates this requirement, in the past we have received designs that are limited to only one type of food (like nuts) or have received designs that are too floral or leafy (and not grounded to food
- Please ensure that you submit designs for all three packaging formats, it is critical to see the family look from the on-set

Target Market(s)

The brand is targeting both mothers and professional chefs and therefore the label design should be broadly approachable and convey affordable premium

Industry/Entity Type

Business

Requirements
Must have
• - Consistent with the brand name and logo, the overall look and feel of the packaging should convey values of healthy, gourmet food ingredients, high in nourishment and project a sense of delightful taste
• - The design styling to be modern and 'simplistic' (embracing 'less-is-more' type of a design style)
• - Design a packaging architecture that incorporates the brand logo together with its tagline lock-up of 'taste the goodness in every spoonful' - find logo attached
• - The design needs to have a dedicated area to print the ingredient (e.g., Mixed Nuts), weight (e.g., 500g) and expiry (this space needs to be flawlessly incorporated into the design) - this information will be printed either with an inkjet printer or with a rubber stamp so please leave an empty space (the text should not be part of the design, just the area for the text needs to be included in the design)
• - The packaging must include 'Packed By: Kestomar Traders Ltd, P. O. Box 51946, Kampala - Uganda'
• - For the design of the resealable pouch, please incorporate a window to see through the ingredients and a hole on top to hang on supermarket pegs if necessary
Nice to have
• - We would love to have some design submissions that are bold and cheerful and fun (but not frivolous) - please see attached inspiration for 'fun' packaging. The attachments are purely for inspiration, not to infringe on anyone else's TM and copyrights
• - Incorporate green to convey healthy, organic values
• - Explore use of gold and silver convey premiumness
Should not have
• - Do not duplicate the tagline
• - Do not include the ingredient, weight and expiry in the main graphic of the design, these will be printed at the time of packing so ensure there is provision for this in a flawless way in the design (e.g., via a blank space allocated for this purpose)

```html
<!DOCTYPE html>
<html lang="en">
<head>
<meta charset="utf-8">
<title>Savorine Label Family</title>
<link rel="stylesheet" href="https://fonts.googleapis.com/css2?family=Oswald:wght@400;500;700&family=Montserrat:wght@800&display=swap">
<style>
  :root {
    --brown: #4a2a14;
    --brown-deep: #3d220f;
    --brown-warm: #5b3619;
    --green: #98bf4c;
    --green-text: #5a9a2e;
    --white: #ffffff;
    --window: #5b5b5b;
    --muted: #6f4a2e;
  }
  * { box-sizing: border-box; margin: 0; padding: 0; }
  html, body { width: 1200px; height: 1200px; overflow: hidden; background: var(--white); }
  .canvas { position: relative; width: 1200px; height: 1200px; }

  .pattern {
    position: absolute; inset: 0;
    background: linear-gradient(135deg, var(--brown-warm), var(--brown) 55%, var(--brown-deep));
  }
  .brand-band {
    position: absolute; background: var(--white);
    display: flex; flex-direction: column; align-items: center; justify-content: flex-end;
  }
  .brand-name {
    font-family: "Oswald", sans-serif; font-weight: 700; color: var(--brown);
    letter-spacing: 0.1em; padding-left: 0.1em; line-height: 1; white-space: nowrap;
  }
  .tagline {
    font-family: "Montserrat", sans-serif; font-weight: 800; color: var(--green-text);
    text-transform: uppercase; letter-spacing: 0.12em; padding-left: 0.12em; white-space: nowrap;
  }
  .label-caption {
    font-family: "Oswald", sans-serif; font-weight: 400; text-transform: uppercase;
  }

  /* Round lid label */
  .lid {
    position: absolute; left: 111px; top: 89px; width: 400px; height: 400px;
    border-radius: 50%; overflow: hidden; border: 3px solid var(--brown-deep);
  }
  .lid .brand-band { left: 0; top: 88px; width: 400px; height: 198px; padding-bottom: 24px; }
  .lid .brand-name { font-size: 70px; }
  .lid .tagline { font-size: 12px; margin-top: 10px; }
  .lid-best-before {
    position: absolute; left: 106px; top: 30px; width: 187px; height: 26px;
    background: var(--green); border-radius: 50% 50% 12px 12px / 100% 100% 12px 12px;
    color: var(--white); font-family: "Oswald", sans-serif; font-size: 9px; font-weight: 500;
    text-align: center; padding-top: 4px;
  }
  .lid-info-strip {
    position: absolute; left: 64px; top: 302px; width: 267px; height: 42px;
    background: var(--green); border-radius: 14px 14px 50% 50% / 14px 14px 100% 100%;
    display: flex; justify-content: center; color: var(--white);
    font-family: "Oswald", sans-serif; font-size: 16px; font-weight: 500;
  }
  .lid-info-strip span { padding: 6px 6px 0; }
  .lid-info-strip .divider { width: 1px; background: var(--white); padding: 0; margin-top: 4px; height: 34px; }
  .lid-packed { position: absolute; inset: 0; }

  /* Square lid label */
  .tub {
    position: absolute; left: 58px; top: 549px; width: 472px; height: 308px;
    border: 3px solid var(--brown-deep); overflow: hidden;
  }
  .tub .brand-band { left: 3px; top: 34px; width: 460px; height: 198px; padding-bottom: 14px; }
  .tub .brand-name { font-size: 72px; }
  .tub .tagline { font-size: 12px; margin-top: 8px; }
  .tub-field {
    position: absolute; top: 238px; width: 130px; height: 44px;
    border: 2px solid var(--green); border-radius: 4px; background: var(--brown);
    color: var(--muted); font-size: 8.5px; padding: 4px 6px;
  }
  .tub-packed {
    position: absolute; left: 3px; top: 288px; width: 460px; height: 13px;
    background: var(--green); color: var(--white); font-family: "Oswald", sans-serif;
    font-size: 7px; line-height: 13px; padding-left: 12px; white-space: nowrap;
  }
  .tub-packed strong { font-weight: 700; font-size: 8px; margin-right: 3px; }

  /* Stand-up pouch */
  .pouch {
    position: absolute; left: 599px; top: 200px; width: 576px; height: 863px;
    border: 3px solid var(--brown-deep); overflow: hidden;
  }
  .pouch .brand-band { left: 0; top: 98px; width: 570px; height: 292px; padding-bottom: 28px; }
  .pouch .brand-name { font-size: 98px; }
  .pouch .tagline { font-size: 17px; margin-top: 14px; }
  .pouch-field {
    position: absolute; left: -2px; width: 151px; height: 81px;
    border: 3px solid var(--green); border-left: none; border-radius: 0 12px 12px 0;
    background: var(--brown); color: var(--muted); font-size: 15px; padding: 6px 8px;
  }
  .pouch-window {
    position: absolute; left: 282px; top: 444px; width: 259px; height: 339px;
    background: var(--window); border: 3px solid var(--green); border-radius: 14px;
  }
  .pouch-packed {
    position: absolute; left: 0; top: 821px; width: 570px; height: 36px;
    background: var(--green); color: var(--white); font-family: "Oswald", sans-serif;
    display: flex; align-items: center; padding-left: 13px; white-space: nowrap;
  }
  .pouch-packed strong { font-weight: 700; font-size: 21px; margin-right: 16px; }
  .pouch-packed span { font-size: 12px; }
</style>
</head>
<body>
<div class="canvas">

  <section class="lid">
    <div class="pattern" role="img" aria-label="Illustrated pattern of nuts and leaves on brown"></div>
    <div class="lid-best-before">BEST BEFORE:</div>
    <div class="brand-band">
      <div class="brand-name">SAVORINE</div>
      <div class="tagline">Taste the goodness in every spoonful</div>
    </div>
    <div class="lid-info-strip">
      <span>INGREDIENTS</span><span class="divider"></span><span>NET WEIGHT</span>
    </div>
    <svg class="lid-packed" viewBox="0 0 400 400">
      <defs><path id="lidArc" d="M 88 360 A 230 230 0 0 0 330 330"/></defs>
      <text font-family="Oswald, sans-serif" font-size="8" fill="#ffffff">
        <textPath href="#lidArc"><tspan font-weight="700" font-size="10">PACKED BY </tspan>KESTOMAR TRADERS LTD, P. O. BOX 51946, KAMPALA - UGANDA</textPath>
      </text>
    </svg>
  </section>

  <section class="tub">
    <div class="pattern" role="img" aria-label="Illustrated pattern of nuts and leaves on brown"></div>
    <div class="brand-band">
      <div class="brand-name">SAVORINE</div>
      <div class="tagline">Taste the goodness in every spoonful</div>
    </div>
    <div class="tub-field label-caption" style="left:15px">Ingredients</div>
    <div class="tub-field label-caption" style="left:169px">Best before</div>
    <div class="tub-field label-caption" style="left:324px">Net weight</div>
    <div class="tub-packed"><strong>PACKED BY</strong>KESTOMAR TRADERS LTD, P. O. BOX 51946, KAMPALA - UGANDA</div>
  </section>

  <section class="pouch">
    <div class="pattern" role="img" aria-label="Illustrated pattern of nuts and leaves on brown"></div>
    <div class="brand-band">
      <div class="brand-name">SAVORINE</div>
      <div class="tagline">Taste the goodness in every spoonful</div>
    </div>
    <div class="pouch-field label-caption" style="top:471px">Ingredients</div>
    <div class="pouch-field label-caption" style="top:573px">Best before:</div>
    <div class="pouch-field label-caption" style="top:675px">Net weight</div>
    <div class="pouch-window" role="img" aria-label="See-through window showing the product"></div>
    <div class="pouch-packed"><strong>PACKED BY</strong><span>KESTOMAR TRADERS LTD, P. O. BOX 51946, KAMPALA - UGANDA</span></div>
  </section>

</div>
</body>
</html>
```